Financial Planning business needs a Web Design

Web design needed for financial planning business that encompasses investments, insurance and corporate planning. Would like a sleek, simple design that includes elements of nature/trees and lifestyle based imagery, with an overall feel of trustworthiness, security, growth and freedom. We like the layout of www.quellmarkroanefinancial.example, torvinfinancial.example and plomtavery.example, but with more color and images consistent with the nature/lifestyle theme.

Target Market(s)

New and existing clients

Industry/Entity Type

Financial

Number of Pages Required

5+ page

Requirements
Nice to have
• link to twitter feed
• 'latest features' link to articles
• links to action - buy insurance, get a quote, etc/

```html
<!DOCTYPE html>
<html lang="en">
<head>
<meta charset="utf-8">
<title>Halverton Wealth Planning</title>
<link rel="stylesheet" href="https://fonts.googleapis.com/css2?family=Open+Sans:ital,wght@0,400;0,600;0,700;1,400&family=Arimo:ital,wght@0,400;0,700;1,400&family=Dancing+Script&display=swap">
<style>
:root{
  --green:#5fb21f;
  --green-dark:#3f8a12;
  --ink:#222;
  --body:#666;
  --banner:#4a4d52;
  --footer:#222;
  --footer-text:#ccc;
  --white:#fff;
}
*{margin:0;padding:0;box-sizing:border-box}
html,body{width:848px;height:1200px;overflow:hidden;background:var(--white)}
body{position:relative;font-family:Arimo,Arial,sans-serif;color:var(--body)}
.abs{position:absolute}
.top-rule{left:0;top:0;width:848px;height:2px;background:#555}
.brand{left:70px;top:28px;display:flex;align-items:center;gap:8px}
.brand-mark{width:26px;height:26px;background:var(--green)}
.brand-name{font-family:'Open Sans',sans-serif;font-weight:600;font-size:19px;color:var(--green-dark);line-height:1}
.phone{right:70px;top:37px;display:flex;align-items:center;gap:8px;font-family:'Open Sans',sans-serif;font-size:12px;color:#555}
.phone .label{color:var(--green);font-size:9px}
.nav{left:0;top:88px;width:848px;height:39px;background:linear-gradient(#f7f7f7,#e6e6e6);border-top:1px solid #e2e2e2;box-shadow:0 2px 3px rgba(0,0,0,.15)}
.nav a{position:absolute;top:14px;font-family:'Open Sans',sans-serif;font-size:9.6px;color:#333;text-decoration:none}
.nav a.active{color:var(--green)}
.hero{left:0;top:127px;width:848px;height:315px;background:linear-gradient(100deg,#58a81c 0%,#8fcf5a 45%,#6dbd2c 70%,#3f8a12 100%)}
.hero-title{left:70px;top:388px;font-family:'Open Sans',sans-serif;font-weight:600;font-size:21px;color:var(--white);text-shadow:0 1px 2px rgba(0,0,0,.4)}
.hero-arrows{left:746px;top:382px}
.section-title{font-family:'Open Sans',sans-serif;font-weight:600;font-size:16px;color:var(--ink)}
.section-title span{color:var(--green)}
.rule{height:1px;background:#ddd}
.rule i{display:block;width:22px;height:1px;background:var(--green)}
.copy{font-size:7.4px;line-height:14.4px;color:var(--body);text-align:justify}
.thumb{left:73px;top:518px;width:135px;height:80px;border:3px solid #fff;box-shadow:0 0 0 1px #ccc;background:linear-gradient(135deg,#2d4f8c,#9fb3d6 50%,#1c2c4e)}
.btn-read{left:73px;top:668px;width:55px;height:22px;background:var(--green);color:#fff;font-size:7.6px;display:flex;align-items:center;justify-content:center}
.news-item{left:570px;width:200px;height:46px}
.date{position:absolute;left:0;top:0;width:32px;height:45px;border:1px solid #ccc;text-align:center}
.date b{display:block;height:28px;font-family:'Open Sans',sans-serif;font-style:italic;font-weight:400;font-size:14px;line-height:28px;color:#333}
.date em{display:block;height:16px;background:#555;color:#fff;font-style:normal;font-size:7px;line-height:16px}
.news-text{position:absolute;left:52px;top:0;width:150px;font-size:7.2px;line-height:14px}
.news-text strong{font-weight:400;color:#222}
.banner{left:69px;top:730px;width:709px;height:65px;border-radius:3px;background:linear-gradient(#555a60,#3e4146)}
.banner p{position:absolute;left:33px;top:16px;width:490px;font-style:italic;font-size:9.4px;line-height:17px;color:#fff}
.btn-buy{position:absolute;left:539px;top:16px;width:128px;height:32px;border-radius:3px;background:linear-gradient(#6cc425,#4c9a16);color:#fff;font-weight:700;font-size:10px;display:flex;align-items:center;justify-content:center;letter-spacing:.3px}
.avatar{left:117px;top:837px;width:60px;height:60px;border-radius:50%;background:radial-gradient(circle at 50% 40%,#d8c4b4,#5a5f68 70%)}
.quote{left:206px;top:845px;width:516px;font-size:7.4px;line-height:14.4px}
.quote-mark{font-family:Georgia,serif;color:#bbb;font-size:16px;line-height:0}
.author{left:206px;top:892px;font-family:'Dancing Script',cursive;font-size:12px;color:var(--green)}
.footer{left:0;top:946px;width:848px;height:254px;background:var(--footer);border-top:2px solid #111}
.f-col{top:980px;font-size:7.4px;line-height:14.4px;color:var(--footer-text)}
.f-col h3{font-family:'Open Sans',sans-serif;font-weight:600;font-size:10.4px;color:#fff;margin-bottom:9px}
.f-col .hl{color:var(--green)}
.f-list li{list-style:none;display:flex;gap:8px;margin-bottom:14px}
.dot{flex:none;width:6px;height:6px;border-radius:50%;background:#fff;margin-top:4px}
.f-field{width:140px;height:19px;border:1px solid #ccc;color:#fff;font-size:6.6px;padding-left:7px;line-height:17px;margin-bottom:8px}
.f-submit{width:44px;height:19px;border:1px solid #ccc;color:#fff;font-size:6.6px;line-height:17px;text-align:center}
.copyright{left:70px;top:1169px;font-size:7.6px;color:#ccc}
.social{top:1162px;width:24px;height:24px}
.bottom-band{left:0;top:1195px;width:848px;height:5px;background:var(--green)}
</style>
</head>
<body>
<div class="abs top-rule"></div>

<header>
  <div class="abs brand"><span class="brand-mark"></span><span class="brand-name">Halverton</span></div>
  <div class="abs phone">
    <svg width="20" height="14" viewBox="0 0 20 14"><path d="M1 5 Q10 -2 19 5 L17 7 L14 5 L14 3 Q10 1.5 6 3 L6 5 L3 7 Z" fill="#555"/><rect x="5" y="7" width="10" height="6" rx="1" fill="#555"/><circle cx="10" cy="10" r="1.8" fill="#fff"/></svg>
    <span><span class="label">Call Us:</span> 555-014-2287</span>
  </div>
</header>

<nav class="abs nav">
  <a class="active" style="left:76px">HOME</a>
  <a style="left:146px">ABOUT US</a>
  <a style="left:232px">WHAT WE DO</a>
  <a style="left:332px">SERVICES</a>
  <a style="left:414px">ARTICLES</a>
  <a style="left:496px">TEAM</a>
  <a style="left:562px">NEWSLETTER</a>
  <a style="left:661px">CONTACT</a>
  <a style="left:745px">LOGIN</a>
</nav>

<section class="abs hero" role="img" aria-label="Green-tinted photo of city office towers seen from street level"></section>
<h1 class="abs hero-title">HALVERTON WEALTH PLANNING</h1>
<svg class="abs hero-arrows" width="34" height="20" viewBox="0 0 34 20"><path d="M10 2 L3 10 L10 18" stroke="#fff" stroke-width="3" fill="none"/><path d="M24 2 L31 10 L24 18" stroke="#fff" stroke-width="3" fill="none"/></svg>

<section class="welcome">
  <h2 class="abs section-title" style="left:74px;top:471px">WELCOME TO <span>HALVERTON</span></h2>
  <div class="abs rule" style="left:74px;top:497px;width:444px"><i></i></div>
  <div class="abs thumb" role="img" aria-label="Photo of two business people in front of glass towers"></div>
  <p class="abs copy" style="left:221px;top:516px;width:297px">Lorem ipsum dolor sit amet, consectetuer adipiscing elit. Aenean commodo ligula eget dolor. Aenean massa. Cum sociis natoque penatibus et magnis dis parturient montes, nascetur ridiculus mus. Donec quam felis, ultricies nec, pellentesque eu, pretium quis, sem. Nulla consequat massa quis enim. Donec pede justo, fringilla vel, aliquet nec, vulputate eget, arcu. In enim justo ridiculus mus. Donec quam felis, ultricies nec, pellentesque eu, pretium quis, sem. Nulla consequat massa quis enim.</p>
  <p class="abs copy" style="left:73px;top:614px;width:445px">Lorem ipsum dolor sit amet, consectetuer adipiscing elit. Aenean commodo ligula eget dolor. Aenean massa. Cum sociis natoque penatibus et magnis dis parturient montes, nascetur ridiculus mus. Donec quam felis, ultricies nec, pellentesque eu, pretium quis, sem. Nulla consequat massa quis enim.</p>
  <a class="abs btn-read">Read More</a>
</section>

<section class="news">
  <h2 class="abs section-title" style="left:571px;top:471px">LATEST <span>NEWS</span></h2>
  <div class="abs rule" style="left:571px;top:497px;width:198px"><i></i></div>
  <div class="abs news-item" style="top:520px"><div class="date"><b>28</b><em>NOV</em></div><p class="news-text"><strong>Consectetuer adipiscing elit. Aenean comm</strong><br>Ligula eget dolor. Aenean massa. Cum sociis natoque penatibus et magnis dis</p></div>
  <div class="abs news-item" style="top:582px"><div class="date"><b>29</b><em>SEP</em></div><p class="news-text"><strong>Consectetuer adipiscing elit. Aenean comm</strong><br>Ligula eget dolor. Aenean massa. Cum sociis natoque penatibus et magnis dis</p></div>
  <div class="abs news-item" style="top:644px"><div class="date"><b>27</b><em>AUG</em></div><p class="news-text"><strong>Consectetuer adipiscing elit. Aenean comm</strong><br>Ligula eget dolor. Aenean massa. Cum sociis natoque penatibus et magnis dis</p></div>
</section>

<section class="abs banner">
  <p>Lorem ipsum dolor sit amet, consectetuer adipiscing elit. Aenean commodo ligula eget dolor. Aenean massa. Cum sociis penatibus et magnis dis parturient montes, nascetur ridiculus mus donec quam felis.</p>
  <a class="btn-buy">BUY INSURANCE</a>
</section>

<section class="testimonial">
  <svg class="abs" style="left:70px;top:858px" width="12" height="20" viewBox="0 0 12 20"><path d="M10 2 L2 10 L10 18" stroke="#bbb" stroke-width="2.5" fill="none"/></svg>
  <svg class="abs" style="left:764px;top:858px" width="12" height="20" viewBox="0 0 12 20"><path d="M2 2 L10 10 L2 18" stroke="#bbb" stroke-width="2.5" fill="none"/></svg>
  <div class="abs avatar" role="img" aria-label="Portrait photo of the client giving the testimonial"></div>
  <span class="abs quote-mark" style="left:190px;top:862px">&ldquo;</span>
  <p class="abs quote">Lorem ipsum dolor sit amet, consectetuer adipiscing elit. Aenean commodo ligula eget dolor. Aenean massa. Cum sociis natoque penatibus et magnis dis parturient montes, nascetur ridiculus mus. Donec quam felis, ultricies nec, pellentesque eu, pretium quis, sem. Nulla consequat massa quis enim. Donec pede justo, fringilla vel, aliquet nec, vulputate eget, arcu. In enim justo. <span class="quote-mark">&rdquo;</span></p>
  <span class="abs author">&ndash; Mara Quill</span>
</section>

<footer class="abs footer"></footer>
<div class="abs f-col" style="left:70px;width:120px">
  <h3>Contact Us</h3>
  <p>Fusce dapibus, tellus condimentum utellus fermalsuada magna. Fusce dapibus, tellus magna.</p>
  <p style="margin-top:8px;padding-left:15px;position:relative"><svg style="position:absolute;left:0;top:3px" width="6" height="8" viewBox="0 0 6 8"><path d="M3 8 L0.5 3.5 A2.5 2.5 0 1 1 5.5 3.5 Z" fill="#5fb21f"/></svg>Address : Lorem ipsum Street<br>Brindlemoor, NSW 2990</p>
  <p style="padding-left:15px;position:relative"><svg style="position:absolute;left:0;top:4px" width="8" height="6" viewBox="0 0 8 6"><path d="M0 2 Q4 -1 8 2 L7 3 L5 2 L3 2 L1 3 Z M2 3 H6 V6 H2 Z" fill="#5fb21f"/></svg>(555)-018-3346</p>
  <p style="padding-left:15px;position:relative;white-space:nowrap"><svg style="position:absolute;left:0;top:4px" width="8" height="6" viewBox="0 0 8 6"><rect width="8" height="6" fill="#5fb21f"/><path d="M0 0 L4 3.5 L8 0" stroke="#222" fill="none"/></svg>info@halvertonwealth.example</p>
</div>
<div class="abs f-col" style="left:250px;width:160px">
  <h3>Latest Tweets</h3>
  <ul class="f-list">
    <li><span class="dot"></span><span>Aenean lacinia bibendum nulla sed leo posuere erat a ante venenatis dapibus <span class="hl">posuere velit aliquet.</span></span></li>
    <li><span class="dot"></span><span>Donec ullamcorper metus auctor fringilla. Nullam <span class="hl">quis risus eget.</span></span></li>
    <li><span class="dot"></span><span><span class="hl">Vestibulum id ligula</span> porta euismod semper. Maecenas faucibus mollis.</span></li>
  </ul>
</div>
<div class="abs f-col" style="left:464px;width:125px">
  <h3>Latest Articles</h3>
  <p>Vivamus sagittis lacus vel augue rutrum dolor auctor.<br><span class="hl" style="font-size:6.8px">Mara Quill</span></p>
  <p style="margin-top:8px">Scelerisque nisl consectetur et.<br><span class="hl" style="font-size:6.8px">Mara Quill</span></p>
  <p style="margin-top:8px">Pellentesque ornare sem lacinia quam venenatis vestibulum. Fusce dapibus,<br><span class="hl" style="font-size:6.8px">Mara Quill</span></p>
</div>
<div class="abs f-col" style="left:638px;width:140px">
  <h3>Get a Quote</h3>
  <div class="f-field">NAME</div>
  <div class="f-field">EMAIL ADDRESS</div>
  <div class="f-submit">SUBMIT</div>
</div>
<p class="abs copyright">&copy; Copyright 2015 &nbsp; Halverton Wealth Planning | All Right Reserved.</p>
<span class="abs social" style="left:646px;background:#3b5998"></span>
<span class="abs social" style="left:673px;background:#3aa3e3"></span>
<span class="abs social" style="left:700px;background:#d13b2c"></span>
<span class="abs social" style="left:727px;background:#c4302b"></span>
<span class="abs social" style="left:754px;background:#8a8a8a"></span>
<div class="abs bottom-band"></div>
</body>
</html>
```